Sea Shipping Logistics Company

The business is a logistics company (sea shipping and other special logistics) and also sales of bulk building materials.
The Design should be minimalistic and give a feeling of power and connectivity.
When the client sees the card, they should get a feeling of confident. Dark overall color (background) and print should be red / white .See logo. The card will be printed on trifecta with the middle color being red.

One side should be the logo and a 5 / 6 word slogan
And other side name, contact (phone/email) and a QR Code.

Target Market(s)

Construction companies / Oil & Gas related companies

Industry/Entity Type

Sea Bulk Shipping Logistics

Contact Information for Business Card

Name, Telephone number, Email address, Website URL, QR Code (see description)

Font styles to use
Sans Serif

Requirements
Must have
• No idea
Nice to have
• Minimalistic, but strong and powerful look and feel.

```html
<!DOCTYPE html>
<html lang="en">
<head>
<meta charset="utf-8">
<title>Korven business card</title>
<link rel="stylesheet" href="https://fonts.googleapis.com/css2?family=Montserrat:wght@400;500;700;800&display=swap">
<style>
  :root {
    --stage: #2b2c2e;
    --card: #1c1d1f;
    --red: #ee3a31;
    --white: #ffffff;
  }
  * { box-sizing: border-box; margin: 0; padding: 0; }
  html, body { width: 1200px; height: 1015px; overflow: hidden; }
  body {
    background: var(--stage);
    font-family: "Montserrat", Arial, sans-serif;
    position: relative;
  }
  .card {
    position: absolute;
    left: 250px;
    width: 700px;
    height: 400px;
    background: var(--card);
    box-shadow: 0 10px 30px rgba(0,0,0,.5);
    overflow: hidden;
  }
  .card::after {
    content: "";
    position: absolute;
    left: 0; right: 0; bottom: 0;
    height: 9px;
    background: var(--red);
  }
  .card-front { top: 55px; }
  .card-back { top: 530px; }

  /* front */
  .brand {
    position: absolute;
    left: 0; right: 0;
    top: 125px;
    display: flex;
    justify-content: center;
    align-items: center;
    gap: 24px;
  }
  .brand-square {
    width: 115px;
    height: 115px;
    border: 3px solid var(--white);
    flex: none;
  }
  .brand-name {
    color: var(--white);
    font-weight: 800;
    font-size: 66px;
    line-height: 1;
    letter-spacing: 1px;
  }
  .brand-tagline {
    color: var(--white);
    font-weight: 400;
    font-size: 15px;
    letter-spacing: 1.5px;
    margin-top: 8px;
  }

  /* back */
  .holder {
    position: absolute;
    left: 40px;
    top: 128px;
    display: flex;
    align-items: stretch;
    gap: 14px;
  }
  .holder-marker { width: 34px; background: var(--red); }
  .holder-name {
    color: var(--red);
    font-weight: 700;
    font-size: 25px;
    letter-spacing: .5px;
    line-height: 1.1;
  }
  .holder-role {
    color: var(--white);
    font-weight: 500;
    font-size: 19px;
    line-height: 1.2;
  }
  .contacts {
    position: absolute;
    left: 140px;
    top: 270px;
    list-style: none;
  }
  .contacts li {
    display: flex;
    align-items: center;
    gap: 10px;
    color: var(--white);
    font-size: 17px;
    font-weight: 500;
    height: 29px;
  }
  .contacts svg { width: 24px; height: 24px; flex: none; }
  .accent { color: var(--red); }
  .mark-frame {
    position: absolute;
    right: 45px;
    top: 55px;
    width: 230px;
    height: 230px;
    border: 5px solid var(--white);
  }
</style>
</head>
<body>

<section class="card card-front" aria-label="Card front">
  <div class="brand">
    <div class="brand-square" aria-hidden="true"></div>
    <div>
      <div class="brand-name">KORVEN</div>
      <div class="brand-tagline">FREIGHT &amp; MARINE</div>
    </div>
  </div>
</section>

<section class="card card-back" aria-label="Card back">
  <div class="holder">
    <div class="holder-marker" aria-hidden="true"></div>
    <div>
      <div class="holder-name">DANIEL MORROW</div>
      <div class="holder-role">Managing Director</div>
    </div>
  </div>

  <ul class="contacts">
    <li>
      <svg viewBox="0 0 24 24" fill="none" stroke="var(--red)" stroke-width="1.5" aria-hidden="true">
        <rect x="1" y="1" width="22" height="22"/>
        <path d="M8 6l2 3-1.5 1.5a8 8 0 0 0 5 5L15 14l3 2-1.5 2.5C11 18 6 13 5.5 7.5z" fill="var(--red)" stroke="none"/>
      </svg>
      044-987 654 321
    </li>
    <li>
      <svg viewBox="0 0 24 24" fill="none" stroke="var(--red)" stroke-width="1.5" aria-hidden="true">
        <rect x="1" y="1" width="22" height="22"/>
        <rect x="5" y="7" width="14" height="10"/>
        <path d="M5 7l7 6 7-6"/>
      </svg>
      info@korven.com
    </li>
    <li>
      <svg viewBox="0 0 24 24" fill="none" stroke="var(--red)" stroke-width="1.5" aria-hidden="true">
        <rect x="1" y="1" width="22" height="22"/>
        <circle cx="12" cy="12" r="6.5"/>
        <ellipse cx="12" cy="12" rx="3" ry="6.5"/>
        <path d="M5.5 12h13"/>
      </svg>
      <span>www.<span class="accent">korven</span>.com</span>
    </li>
  </ul>

  <div class="mark-frame" aria-hidden="true"></div>
</section>

</body>
</html>
```